Alapca breeding needs a website

Presentation of the farm, animals (stallions, mares, information about the animals, for sale) and possible later expansion with a webshop (alpaca wool products). We want to present our farm and the animals on the farm on this page. A mission why we are doing this. Furthermore, each animal should be shown with a picture and described. Later we want to sell our own products made from alpaca wool via a webshop. But we still need to grow a bit to do that.

Target Market(s)

Information about my alpaca breeding and the alpaca farm

Industry/Entity Type

Tierzucht

Number of Pages Required

1 page

Font styles to use
Sans Serif

Requirements
Must have
• Modern design that matches the logo
Nice to have
• Intuitive operation / Clear structure
Should not have
• No

```html
<!DOCTYPE html>
<html lang="en">
<head>
<meta charset="utf-8">
<title>Lumera Alpaca</title>
<link href="https://fonts.googleapis.com/css2?family=Cinzel:wght@400;600&family=Montserrat:wght@400;500;600&family=Roboto:wght@400;500&display=swap" rel="stylesheet">
<style>
:root{
  --green:#7ab536;
  --green-dark:#5f9a24;
  --navy:#10305c;
  --navy-deep:#0b2749;
  --ink:#13294b;
  --text:#333a44;
  --muted:#f3f3f3;
  --white:#ffffff;
  --star:#f5a623;
}
*{box-sizing:border-box;margin:0;padding:0}
html,body{width:1200px;height:3625px;overflow:hidden}
body{position:relative;background:var(--white);font-family:'Montserrat',sans-serif;color:var(--text)}
.abs{position:absolute}
.serif{font-family:'Cinzel',serif}
.btn{position:absolute;background:var(--green);color:var(--white);font-family:'Cinzel',serif;font-weight:600;font-size:15px;display:flex;align-items:center;justify-content:center;border-radius:3px;letter-spacing:.5px}

/* header */
.brand{left:118px;top:40px;width:110px;display:flex;flex-direction:column;align-items:center;gap:6px}
.brand-dot{width:40px;height:40px;border-radius:50%;background:var(--navy)}
.brand-name{font-family:'Montserrat',sans-serif;font-weight:600;font-size:19px;color:var(--navy);letter-spacing:1px}
.phone{left:686px;top:32px;display:flex;align-items:center;gap:12px;font-size:15px;font-weight:600;color:#222}
.phone-ico{width:30px;height:30px;border-radius:50%;background:var(--green);display:flex;align-items:center;justify-content:center}
.nav{top:96px;font-size:14px;font-weight:500;color:#222;letter-spacing:.3px}

/* hero */
.hero{left:0;top:137px;width:1200px;height:640px;background:radial-gradient(ellipse at 65% 40%,#c98a4a 0%,#8a5530 30%,#4b2c1a 70%,#2e1b10 100%)}
.hero-title{left:112px;color:var(--white)}
.section-title{font-family:'Cinzel',serif;font-size:39px;color:var(--ink);letter-spacing:1px;word-spacing:14px;white-space:nowrap}
.para{font-size:14px;line-height:25.6px;text-align:justify}

/* animals */
.animals{left:0;top:1328px;width:1200px;height:642px;background:linear-gradient(180deg,var(--navy) 0%,#15386a 55%,var(--navy-deep) 100%)}
.card-img{position:absolute;width:376px;height:249px;border-radius:6px}
.card-name{position:absolute;font-family:'Cinzel',serif;font-size:26px;color:var(--white)}
.card-desc{position:absolute;width:376px;font-size:15px;line-height:26px;color:var(--white)}
.arrow{position:absolute;width:42px;height:42px;border:2px solid var(--green);border-radius:50%}

/* form */
.field{position:absolute;background:var(--white);border-radius:6px;box-shadow:0 2px 8px rgba(0,0,0,.06);font-family:'Roboto',sans-serif;font-size:14px;color:#555;padding:22px 22px}

/* footer */
.foot-h{position:absolute;font-family:'Roboto',sans-serif;font-weight:500;font-size:20px;color:var(--white)}
.foot-list{position:absolute;list-style:none;font-family:'Roboto',sans-serif;font-size:15px;color:var(--white)}
.foot-list li{height:26px;display:flex;align-items:center;gap:12px}
.foot-list li::before{content:"»";font-size:17px}
.foot-info{position:absolute;font-family:'Roboto',sans-serif;font-size:15px;line-height:26px;color:var(--white);display:flex;gap:12px}
.social{position:absolute;width:38px;height:38px;border-radius:50%;background:var(--white)}
</style>
</head>
<body>

<!-- header -->
<div class="abs brand"><span class="brand-dot"></span><span class="brand-name">LUMERA</span></div>
<div class="abs phone"><span class="phone-ico"><svg width="16" height="16" viewBox="0 0 24 24"><path fill="#fff" d="M6.6 10.8a15 15 0 006.6 6.6l2.2-2.2a1 1 0 011-.25 11.4 11.4 0 003.6.57 1 1 0 011 1V20a1 1 0 01-1 1A17 17 0 013 4a1 1 0 011-1h3.5a1 1 0 011 1c0 1.25.2 2.45.57 3.57a1 1 0 01-.25 1z"/></svg></span>+1 (555) 014 2290</div>
<svg class="abs" style="left:912px;top:37px" width="20" height="20" viewBox="0 0 24 24"><circle cx="10" cy="10" r="7" fill="none" stroke="#333" stroke-width="2"/><path d="M15 15l6 6" stroke="#333" stroke-width="2"/></svg>
<svg class="abs" style="left:951px;top:36px" width="22" height="22" viewBox="0 0 24 24"><path d="M2 3h3l2.5 12h11l2-8H6" fill="none" stroke="#333" stroke-width="2"/><circle cx="9" cy="20" r="1.6" fill="#333"/><circle cx="17" cy="20" r="1.6" fill="#333"/></svg>
<div class="btn" style="left:992px;top:28px;width:96px;height:37px">LOG IN</div>
<div class="abs nav" style="left:529px">HOME</div>
<div class="abs nav" style="left:620px">ABOUT US</div>
<div class="abs nav" style="left:744px">SERVICES</div>
<div class="abs nav" style="left:862px">PRODUCTS</div>
<div class="abs nav" style="left:992px">CONTACT US</div>

<!-- hero -->
<div class="abs hero" role="img" aria-label="Alpaca eating hay in a wooden barn, second alpaca beside it"></div>
<svg class="abs" style="left:0;top:600px" width="1200" height="190" viewBox="0 0 1200 190">
  <path d="M0 40 Q600 260 1200 20 V190 H0Z" fill="#fff"/>
  <path d="M0 40 Q600 260 1200 20" fill="none" stroke="var(--green)" stroke-width="7"/>
</svg>
<div class="abs hero-title serif" style="top:275px;font-size:33px;letter-spacing:2px">WELCOME TO</div>
<div class="abs hero-title serif" style="top:322px;font-size:84px;line-height:92px;font-weight:600">LUMERA<br>ALPACA</div>
<div class="btn" style="left:112px;top:532px;width:122px;height:36px">GET STARTED</div>

<!-- mission -->
<div class="abs" style="left:14px;top:816px;width:690px;height:478px;background:radial-gradient(ellipse at 50% 50%,#c9b08a 0%,#e6dccb 45%,#ffffff 75%)" role="img" aria-label="Alpaca silhouettes filled with a sunlit pasture scene"></div>
<div class="abs section-title" style="left:658px;top:882px">OUR MISSION</div>
<p class="abs para" style="left:658px;top:955px;width:430px">Lorem ipsum dolor sit amet, consectetur adipiscing elit, sed do eiusmod tempor incididunt ut labore et dolore magna aliqua. Ut enim ad minim veniam, quis nostrud exercitation ullamco laboris nisi ut aliquip ex ea commodo consequat. Duis aute irure dolor in reprehenderit in voluptate velit esse cillum dolore eu fugiat nulla pariatur. Excepteur sint occaecat cupidatat non proident, sunt in culpa qui officia deserunt mollit anim id est laborum.</p>
<div class="btn" style="left:658px;top:1186px;width:130px;height:38px">LEARN MORE</div>

<!-- animals -->
<div class="abs animals" role="img" aria-label="Herd of alpacas in a field at dusk, tinted navy"></div>
<div class="abs section-title" style="left:0;width:1200px;text-align:center;top:1402px;color:var(--white)">OUR ANIMALS</div>
<div class="arrow" style="left:111px;top:1594px"><svg width="38" height="38" viewBox="0 0 38 38"><path d="M22 12l-7 7 7 7" fill="none" stroke="var(--green)" stroke-width="2"/></svg></div>
<div class="arrow" style="left:1047px;top:1594px"><svg width="38" height="38" viewBox="0 0 38 38"><path d="M16 12l7 7-7 7" fill="none" stroke="var(--green)" stroke-width="2"/></svg></div>

<div class="card-img" style="left:187px;top:1491px;background:linear-gradient(180deg,#cfd8d0 0%,#5f7d3d 35%,#b39c80 60%,#a48a6c 100%)" role="img" aria-label="Brown stallion trotting in a sandy paddock"></div>
<div class="card-name" style="left:186px;top:1760px">STALLIONS</div>
<div class="card-name" style="left:492px;top:1760px">$79</div>
<div class="card-desc" style="left:187px;top:1807px">Lorem ipsum dolor sit amet, consectetur adipiscing elit, sed do eiusmod</div>
<div class="btn" style="left:187px;top:1880px;width:130px;height:36px">ADD TO CART</div>

<div class="card-img" style="left:637px;top:1491px;background:linear-gradient(180deg,#9fb0de 0%,#b7c3e4 45%,#7fae45 70%,#9cbf3a 100%)" role="img" aria-label="Chestnut mare standing in a green meadow"></div>
<div class="card-name" style="left:636px;top:1760px">MARES</div>
<div class="card-name" style="left:942px;top:1760px">$79</div>
<div class="card-desc" style="left:637px;top:1807px">Lorem ipsum dolor sit amet, consectetur adipiscing elit, sed do eiusmod</div>
<div class="btn" style="left:637px;top:1880px;width:130px;height:36px">ADD TO CART</div>

<!-- shop -->
<div class="abs section-title" style="left:112px;top:2081px">OUR SHOP</div>
<div class="abs" style="left:114px;top:2147px;color:var(--star);font-size:13px;letter-spacing:1px">★★★★★</div>
<div class="abs" style="left:114px;top:2174px;color:var(--green-dark);font-size:21px;font-weight:500">$25.00</div>
<p class="abs" style="left:114px;top:2214px;width:440px;font-size:14px;line-height:24px">Lorem ipsum dolor sit amet, consectetur adipiscing elit, sed do eiusmod tempor incididunt ut labore et dolore magna aliqua. Quis ipsum suspendisse ultrices gravida. Risus commodo viverra maecenas accumsan lacus vel facilisis.</p>
<div class="abs" style="left:115px;top:2340px;width:129px;height:44px;border:1px solid #333;border-radius:5px;display:flex;font-size:16px">
  <span style="width:38px;display:flex;align-items:center;justify-content:center;border-right:1px solid #333;font-size:20px">-</span>
  <span style="flex:1;display:flex;align-items:center;justify-content:center">00</span>
  <span style="width:38px;display:flex;align-items:center;justify-content:center;border-left:1px solid #333;font-size:22px">+</span>
</div>
<div class="btn" style="left:112px;top:2417px;width:130px;height:37px">ADD TO CART</div>
<div class="abs" style="left:620px;top:2000px;width:490px;height:250px;background:radial-gradient(ellipse at 50% 70%,rgba(122,181,54,.35) 0%,rgba(122,181,54,0) 70%)" role="img" aria-label="Stylised tree with green leaves growing above the wool circle"></div>
<div class="abs" style="left:640px;top:2114px;width:416px;height:416px;border-radius:50%;border:3px solid var(--navy);background:radial-gradient(circle at 40% 45%,#f3ead8 0%,#d9c6a4 55%,#b29a75 100%)" role="img" aria-label="Close-up of raw cream alpaca wool"></div>
<div class="abs" style="left:1027px;top:2406px;width:173px;height:211px;background:radial-gradient(ellipse at 60% 55%,#b58a5c 0%,#d9bd95 55%,rgba(255,255,255,0) 75%)" role="img" aria-label="Alpaca peeking in from the right edge"></div>

<!-- contact -->
<div class="abs" style="left:0;top:2617px;width:1200px;height:620px;background:var(--muted)"></div>
<div class="abs" style="left:0;top:2476px;width:295px;height:218px;background:radial-gradient(ellipse at 45% 55%,#e9e3d8 0%,#d8cfc0 45%,rgba(243,243,243,0) 75%)" role="img" aria-label="Two white llamas standing"></div>
<div class="abs section-title" style="left:0;width:1200px;text-align:center;top:2686px">CONTACT US</div>
<div class="field" style="left:204px;top:2772px;width:383px;height:62px">Name</div>
<div class="field" style="left:611px;top:2772px;width:384px;height:62px">Phone Number</div>
<div class="field" style="left:204px;top:2859px;width:383px;height:62px">Email</div>
<div class="field" style="left:611px;top:2859px;width:384px;height:62px;display:flex;justify-content:space-between">Select Animals<svg width="10" height="10" viewBox="0 0 10 10"><path d="M2 3l3 3 3-3" fill="none" stroke="#555" stroke-width="1.2"/></svg></div>
<div class="field" style="left:204px;top:2945px;width:792px;height:95px">Message</div>
<div class="btn" style="left:535px;top:3077px;width:130px;height:37px">SUBMIT</div>

<!-- footer -->
<svg class="abs" style="left:0;top:3175px" width="1200" height="450" viewBox="0 0 1200 450">
  <defs><linearGradient id="fg" x1="0" y1="0" x2="0" y2="1"><stop offset="0" stop-color="#15386a"/><stop offset="1" stop-color="#0b2749"/></linearGradient></defs>
  <path d="M0 165 Q600 -150 1200 160 V450 H0Z" fill="url(#fg)"/>
  <path d="M0 165 Q600 -150 1200 160" fill="none" stroke="var(--green)" stroke-width="7"/>
</svg>
<div class="abs" style="left:155px;top:3330px;width:190px;display:flex;flex-direction:column;align-items:center;gap:14px">
  <span style="width:70px;height:70px;border-radius:50%;background:var(--white)"></span>
  <span style="font-family:'Montserrat',sans-serif;font-weight:600;font-size:30px;color:var(--white);letter-spacing:2px">LUMERA</span>
</div>
<div class="abs" style="left:398px;top:3330px;width:1px;height:170px;background:rgba(255,255,255,.25)"></div>
<div class="foot-h" style="left:439px;top:3320px">Navigation</div>
<ul class="foot-list" style="left:439px;top:3358px"><li>Home</li><li>About Us</li><li>Services</li><li>Products</li><li>Contact us</li></ul>
<div class="foot-h" style="left:646px;top:3320px">About Fernhill</div>
<ul class="foot-list" style="left:646px;top:3358px"><li>Terms &amp; Conditions</li><li>Privacy Policy</li><li>About Us</li><li>Contact Us</li></ul>
<div class="foot-h" style="left:871px;top:3320px">Contact us</div>
<div class="foot-info" style="left:871px;top:3359px"><svg width="14" height="20" viewBox="0 0 14 20"><path d="M7 0a7 7 0 00-7 7c0 5 7 13 7 13s7-8 7-13a7 7 0 00-7-7zm0 9.5A2.5 2.5 0 117 4.5a2.5 2.5 0 010 5z" fill="#fff"/></svg><span>Shop 3 5 Lorem ipsum<br>dolor sit amet, consectetur</span></div>
<div class="foot-info" style="left:871px;top:3425px"><svg width="16" height="16" viewBox="0 0 24 24"><path fill="#fff" d="M6.6 10.8a15 15 0 006.6 6.6l2.2-2.2a1 1 0 011-.25 11.4 11.4 0 003.6.57 1 1 0 011 1V20a1 1 0 01-1 1A17 17 0 013 4a1 1 0 011-1h3.5a1 1 0 011 1c0 1.25.2 2.45.57 3.57a1 1 0 01-.25 1z"/></svg><span>+1 (555) 014 2290</span></div>
<div class="foot-info" style="left:871px;top:3467px"><svg width="18" height="14" viewBox="0 0 18 14"><rect width="18" height="14" rx="1.5" fill="#fff"/><path d="M1 1.5l8 6 8-6" fill="none" stroke="#10305c" stroke-width="1.4"/></svg><span>hello@lumeraalpaca.com</span></div>
<div class="abs" style="left:118px;top:3534px;width:964px;height:1px;background:rgba(255,255,255,.15)"></div>
<div class="abs" style="left:0;width:1200px;top:3568px;text-align:center;font-family:'Roboto',sans-serif;font-size:15px;color:var(--white)">©Copyrights 2024 Lumera Alpaca. &nbsp;| &nbsp; All Rights Reserved</div>
<div class="social" style="left:997px;top:3553px"></div>
<div class="social" style="left:1049px;top:3553px"></div>

</body>
</html>
```